Flaschenetiketten-Design in rechteckiger Grundform für Biermanufaktur
Zielgruppe
Wir repräsentieren eine Bier-Manufaktur in der Gründungsphase und sind auf der Suche nach einem Designvorschlag für die Flaschenetiketten.
Unsere Zielgruppe sind Liebhaber, die auf der Suche nach dem Speziellen und Lokalen sind. Der Biergenuss abseits des Massenmarktes soll im Entwurf sichtbar/transportiert werden. Die Bier-Manufaktur steht zeitgleich für Trend-Kreationen mit bodenständigem Ursprung.
Aufgabenstellung
Die Herkunft der Gründer Familie aus dem Schweizer Kanton Simplon soll im Vordergrund stehen, hierzu bitte das Familienwappen / einzelne Elemente siehe Dateiupload berücksichtigen.
Das Etikett soll eine rechteckige Grundform haben.
Folgende Angaben sollen sich im Etikett wiederfinden:
- Biersorte: 'Lager' (zukünftig soll es möglich sein, Biersorte auf dem Etikett zu wechseln)
Brand: 'Hearty Kandrom'
'Biermanufaktur Walliser Ursprungs'
Die Schrift soll klar und nicht zu verspielt sein.

```html
<!DOCTYPE html>
<html lang="de">
<head>
<meta charset="utf-8">
<title>Hearty Kandrom Lager – Flaschenetikett</title>
<link rel="stylesheet" href="https://fonts.googleapis.com/css2?family=Fjalla+One&family=Open+Sans:wght@400;600&family=Pinyon+Script&family=Libre+Baskerville:ital@1&display=swap">
<style>
  :root {
    --stage: #4a4a4a;
    --label-top: #5cc3d3;
    --label-bottom: #3ea8bb;
    --gold: #e3a72a;
    --crest-green: #1f5f4a;
    --ink: #1e3a40;
    --white: #ffffff;
    --muted: #dff3f6;
  }
  html, body {
    margin: 0;
    padding: 0;
    overflow: hidden;
  }
  .canvas {
    width: 1200px;
    height: 580px;
    background: var(--stage);
    display: flex;
    align-items: center;
    justify-content: center;
    overflow: hidden;
  }
  .label {
    width: 420px;
    height: 540px;
    background: linear-gradient(180deg, var(--label-top), var(--label-bottom));
    box-sizing: border-box;
    padding: 18px 30px 20px;
    display: flex;
    flex-direction: column;
  }
  .label__tagline {
    margin: 0;
    text-align: center;
    font-family: "Pinyon Script", cursive;
    font-size: 22px;
    line-height: 1.3;
    color: var(--ink);
  }
  .label__crest {
    display: block;
    margin: 10px 0 0 -8px;
    width: 86px;
    height: 94px;
    flex-shrink: 0;
  }
  .label__brand {
    margin: 12px 0 0;
    font-family: "Fjalla One", sans-serif;
    font-weight: 400;
    color: var(--gold);
    line-height: 1;
  }
  .label__brand-name {
    display: block;
    font-size: 56px;
    letter-spacing: 0.5px;
    white-space: nowrap;
  }
  .label__brand-sub {
    display: block;
    text-align: right;
    font-size: 36px;
    margin-top: 2px;
  }
  .label__variety {
    margin: 4px 0 0;
    text-align: right;
    font-family: "Open Sans", sans-serif;
    font-weight: 400;
    font-size: 50px;
    line-height: 1.1;
    letter-spacing: 2px;
    color: var(--white);
  }
  .label__claim {
    margin: 16px 0 0;
    padding: 8px 0;
    border-top: 2px solid var(--ink);
    border-bottom: 2px solid var(--ink);
    text-align: center;
    font-family: "Open Sans", sans-serif;
    font-size: 20px;
    letter-spacing: 4px;
    color: var(--ink);
  }
  .label__facts {
    margin-top: auto;
    display: flex;
    justify-content: space-between;
    font-family: "Libre Baskerville", serif;
    font-style: italic;
    font-size: 18px;
    color: var(--muted);
  }
</style>
</head>
<body>
<main class="canvas">
  <article class="label">
    <p class="label__tagline">Biermanufaktur Walliser Ursprungs</p>

    <svg class="label__crest" viewBox="0 0 86 94" role="img" aria-label="Familienwappen der Gründerfamilie">
      <rect x="0" y="0" width="86" height="94" rx="6" fill="var(--crest-green)"/>
    </svg>

    <h1 class="label__brand">
      <span class="label__brand-name">Hearty Kandrom</span>
      <span class="label__brand-sub">Bier</span>
    </h1>

    <p class="label__variety">LAGER</p>

    <p class="label__claim">HAND CRAFTED BEER</p>

    <div class="label__facts">
      <span class="label__abv">Alk./Vol. 5,5</span>
      <span class="label__volume">500ml</span>
    </div>
  </article>
</main>
</body>
</html>
```